"Tandem Mouthguards " Custom-made Mouthguard Business Website

We need an informational website for our mouthguard Business "Tandem Mouthguards". The logo is navy blue/lime green so want to have colour scheme that goes nicely with this - have uploaded our mouthguard flyer with some information we need to put into the website but I do have more information to put in there.

Target Market(s)

Sports clubs, sportspeople, parents and kids, schools

Industry/Entity Type

Dental, Custom-made Sports Mouthguards

Coding

Coded - Design and coding required

Number of Pages Required

5+ page

Font styles to use
Serif
Sans Serif

Colors
0054AA
0677BA
7BADD7
CADEEF
E8F1F8
0094D4
00A9DD
6FCCEA
C7EBF8
E9F6FB
00AB8E
00BBA5
67D7C9
C6EFE9
E9F9F6
59FF00
82FF00
B8FF75
E3FFCB
F4FFEA
FFF300
FFF600
FEFA6F
FFFEC7
FFFEE8
FFC000
F8CF3A
FAE287
FDF2CF
FEFAEE
F0912C
F2A743
F7CA91
FBE8D2
FDF5EE
EE7325
F08F49
F5BC92
FAE3D3
FDF4ED

Requirements
Must have
• I want drop down pages, not one scrolling page. Different pages for each heading . Content uploaded - We need a general home page with lots of pictures and info that I'll provide. A page each dedicated to 1) About Us 2) Why choose a custom mouthguard? 3) Gallery 4) Contact Us. Will need logos from "Velora"
Nice to have
• Mainly use greens and blues, but happy to pop in some yellow/oranges/red oranges if it looks good

```html
<!DOCTYPE html>
<html lang="en">
<head>
<meta charset="utf-8">
<title>Tandem Mouthguards</title>
<link href="https://fonts.googleapis.com/css2?family=Poppins:wght@400;500;600;700;800&display=swap" rel="stylesheet">
<style>
:root{
  --navy:#0c2a6b;
  --navy-deep:#0a2260;
  --green:#2fc94f;
  --green-dark:#14a54a;
  --teal:#1fc9c9;
  --yellow:#f6df4a;
  --white:#ffffff;
  --line:#eeeeee;
  --text:#333a4a;
}
*{box-sizing:border-box;margin:0;padding:0}
html,body{width:1200px;height:2624px;overflow:hidden;background:var(--white);font-family:'Poppins',sans-serif;color:var(--text)}
.page{position:relative;width:1200px;height:2624px;overflow:hidden}
.abs{position:absolute}
.media{position:absolute;display:block}

/* hero */
.hero{position:absolute;left:0;top:0;width:1200px;height:660px}
.brand-small{position:absolute;left:112px;top:30px;color:var(--white);font-weight:800;font-size:20px;line-height:1.05;width:160px}
.brand-small small{display:block;font-size:11px;font-weight:800;margin-bottom:4px}
.nav{position:absolute;left:297px;top:37px;width:792px;height:44px;border-radius:22px;background:rgba(20,70,110,.75);display:flex;align-items:center;padding-left:22px}
.nav a{color:var(--white);font-size:12px;font-weight:600;text-decoration:none;margin-right:58px;letter-spacing:.2px}
.nav a.active{color:var(--yellow)}
.nav .contact{position:absolute;right:4px;top:2px;height:40px;width:150px;border-radius:20px;background:var(--green-dark);display:flex;align-items:center;padding-left:22px;margin:0}
.btn{position:absolute;height:46px;border-radius:23px;background:var(--green-dark);color:var(--white);font-size:12px;font-weight:700;display:flex;align-items:center;padding-left:26px;width:152px}
.btn .dot,.nav .dot{position:absolute;right:3px;top:3px;width:40px;height:40px;border-radius:50%;background:var(--navy);display:flex;align-items:center;justify-content:center}
.nav .dot{width:34px;height:34px}
.dot i{width:14px;height:14px;border-radius:50%;border:3px solid var(--white);background:var(--green)}
.hero-name{position:absolute;left:112px;top:150px;width:420px;color:var(--white);font-weight:800;font-size:62px;line-height:1.05;letter-spacing:1px}
.hero-rule{position:absolute;left:112px;top:287px;width:400px;height:2px;background:var(--green)}
.hero h1{position:absolute;left:114px;top:293px;color:var(--white);font-size:38px;font-weight:600;line-height:1.2}
.hero p{position:absolute;left:114px;top:402px;color:var(--white);font-size:15px}

/* why */
.capsule{position:absolute;border:4px solid #f2f2f2}
.h2{font-size:30px;font-weight:700;color:var(--navy);line-height:1.3}
.h2 em{font-style:normal;color:var(--green)}
.ticks{list-style:none}
.ticks li{display:flex;align-items:center;font-size:14px;font-weight:500;color:var(--navy);height:32.5px}
.ticks svg{margin-right:8px}
.outline-word{position:absolute;font-weight:500;font-size:92px;letter-spacing:2px;white-space:nowrap;line-height:1}

/* gap free */
.gap{position:absolute;left:112px;top:1273px;width:976px;height:149px;background:var(--yellow);border-radius:8px}
.gap h3{position:absolute;left:44px;top:36px;font-size:30px;font-weight:700;color:var(--navy);line-height:1.4}
.gap p{position:absolute;left:623px;top:38px;width:290px;font-size:14.5px;color:var(--navy);line-height:1.38}

/* protect */
.body-copy{font-size:13.5px;line-height:1.5;color:#555}

/* game day */
.gameday{position:absolute;left:0;top:1982px;width:1200px;height:420px;background:linear-gradient(90deg,#21ccd2 0%,#2ccf8e 55%,#32cd55 100%)}
.gameday h2{position:absolute;left:0;width:1200px;top:2025px;text-align:center;color:var(--white);font-size:40px;font-weight:600;line-height:1.15}
.gameday-note{position:absolute;left:0;width:1200px;top:2127px;text-align:center;color:var(--white);font-size:12px;line-height:1.4}
.circle{position:absolute;border-radius:50%;border:6px solid var(--white)}

/* footer */
.footer-col h4{font-size:14px;font-weight:600;color:var(--white);margin-bottom:14px}
.footer-col a,.footer-col span{display:block;font-size:9.5px;color:var(--white);text-decoration:none;margin-bottom:9px}
.contact-row{display:flex;align-items:center;font-size:9.5px;color:var(--white);height:35px}
.contact-row b{width:22px;height:22px;border:1.5px solid var(--green);border-radius:50%;margin-right:10px;display:flex;align-items:center;justify-content:center}
</style>
</head>
<body>
<div class="page">

  <!-- hero -->
  <div class="hero">
    <div class="media" style="left:0;top:0;width:1200px;height:660px;background:linear-gradient(180deg,#1c5d6d 0%,#2b7a4a 55%,#3f8b3a 100%)" role="img" aria-label="Two smiling kids in footy jerseys holding a yellow football, wearing coloured mouthguards"></div>
    <svg class="abs" style="left:0;top:0" width="1200" height="660" viewBox="0 0 1200 660">
      <defs><linearGradient id="shade" x1="0" x2="1"><stop offset="0" stop-color="#123f6f" stop-opacity=".85"/><stop offset=".5" stop-color="#123f6f" stop-opacity="0"/></linearGradient></defs>
      <rect width="1200" height="660" fill="url(#shade)"/>
      <path d="M0 520 Q600 760 1200 520 L1200 660 L0 660Z" fill="var(--navy)"/>
      <path d="M0 532 Q600 742 1200 538 L1200 660 L0 660Z" fill="var(--white)"/>
      <path d="M0 520 Q600 700 1200 520" fill="none" stroke="var(--white)" stroke-width="4"/>
    </svg>
    <div class="brand-small"><small>HARBOURLINE DENTURE CARE</small>TANDEM MOUTHGUARDS</div>
    <nav class="nav">
      <a class="active">HOME</a><a>ABOUT US</a><a>OUR MOUTHGUARDS</a><a>PHOTO GALLERY</a><a>FAQ</a>
      <a class="contact">CONTACT US<span class="dot"><i></i></span></a>
    </nav>
    <div class="hero-name">TANDEM MOUTHGUARDS</div>
    <div class="hero-rule"></div>
    <h1>Custom made sports<br>Mouthguards in Perth</h1>
    <p>Protect your smile with a comfortable, professional fit.</p>
    <div class="btn" style="left:114px;top:448px">BOOK NOW<span class="dot"><i></i></span></div>
  </div>

  <!-- why choose -->
  <div class="media" style="left:1125px;top:632px;width:75px;height:150px;border-radius:75px 0 0 75px;background:linear-gradient(135deg,#f5c63a,#e23d3d,#2b9be0)" role="img" aria-label="Rainbow patterned mouthguard"></div>
  <div class="capsule" style="left:410px;top:703px;width:678px;height:374px;border-radius:0 187px 187px 0;border-left:none"></div>
  <div class="media" style="left:112px;top:703px;width:302px;height:359px;background:linear-gradient(135deg,#c9b7d6,#7c4fb3)" role="img" aria-label="Hand holding purple glitter mouthguards"></div>
  <div class="media" style="left:335px;top:857px;width:212px;height:223px;background:linear-gradient(135deg,#47d74c,#f2f2f2);border:4px solid var(--white);border-radius:6px" role="img" aria-label="White mouthguard with team emblem on green model"></div>
  <h2 class="h2 abs" style="left:588px;top:736px">WHY CHOOSE TANDEM<br><em>MOUTHGUARDS?</em></h2>
  <ul class="ticks abs" style="left:588px;top:820px">
    <li><svg width="16" height="16" viewBox="0 0 16 16"><circle cx="8" cy="8" r="8" fill="var(--navy)"/><circle cx="8" cy="8" r="5" fill="var(--green)"/><path d="M5.5 8l1.8 1.8 3.2-3.4" stroke="var(--navy)" stroke-width="1.4" fill="none"/></svg>Professionally made by a qualified dental prosthetist</li>
    <li><svg width="16" height="16" viewBox="0 0 16 16"><circle cx="8" cy="8" r="8" fill="var(--navy)"/><circle cx="8" cy="8" r="5" fill="var(--green)"/><path d="M5.5 8l1.8 1.8 3.2-3.4" stroke="var(--navy)" stroke-width="1.4" fill="none"/></svg>Custom fit for comfort, protection, and durability</li>
    <li><svg width="16" height="16" viewBox="0 0 16 16"><circle cx="8" cy="8" r="8" fill="var(--navy)"/><circle cx="8" cy="8" r="5" fill="var(--green)"/><path d="M5.5 8l1.8 1.8 3.2-3.4" stroke="var(--navy)" stroke-width="1.4" fill="none"/></svg>Wide range of colours and designs</li>
    <li><svg width="16" height="16" viewBox="0 0 16 16"><circle cx="8" cy="8" r="8" fill="var(--navy)"/><circle cx="8" cy="8" r="5" fill="var(--green)"/><path d="M5.5 8l1.8 1.8 3.2-3.4" stroke="var(--navy)" stroke-width="1.4" fill="none"/></svg>Available for kids, teens, and adults</li>
    <li><svg width="16" height="16" viewBox="0 0 16 16"><circle cx="8" cy="8" r="8" fill="var(--navy)"/><circle cx="8" cy="8" r="5" fill="var(--green)"/><path d="M5.5 8l1.8 1.8 3.2-3.4" stroke="var(--navy)" stroke-width="1.4" fill="none"/></svg>Clinic and mobile school/club visits available</li>
  </ul>
  <div class="btn" style="left:588px;top:999px">BOOK NOW<span class="dot"><i></i></span></div>

  <!-- word band -->
  <div class="outline-word" style="left:-40px;top:1157px;color:#eef0f6">TANDEM MOUTHGUARDS</div>
  <div class="media" style="left:862px;top:1045px;width:338px;height:185px;border-radius:60px 0 0 20px;background:linear-gradient(120deg,#e3322f,#f1f1f1 45%,#3f8fd8)" role="img" aria-label="Assorted colourful mouthguards and cases"></div>

  <!-- gap free -->
  <div class="gap">
    <h3>GAP-FREE<br>MOUTHGUARDS</h3>
    <p>If you're with a private health fund, you may be eligible for our gap-free mouthguards. Ask us how you can get the best protection at no extra cost.</p>
  </div>
  <svg class="abs" style="left:502px;top:1265px" width="196" height="170" viewBox="0 0 196 170">
    <circle cx="98" cy="85" r="97" fill="var(--white)"/>
    <circle cx="98" cy="85" r="85" fill="var(--yellow)"/>
    <circle cx="98" cy="85" r="43" fill="var(--navy)"/>
    <circle cx="98" cy="85" r="31" fill="var(--green)"/>
  </svg>

  <!-- protect -->
  <div class="media" style="left:0;top:1410px;width:60px;height:150px;border-radius:0 75px 75px 0;background:linear-gradient(135deg,#7ec8f0,#1f6bc2)" role="img" aria-label="Blue glitter mouthguard"></div>
  <div class="capsule" style="left:112px;top:1482px;width:662px;height:352px;border-radius:176px 0 0 176px;border-right:none"></div>
  <h2 class="h2 abs" style="left:205px;top:1532px;font-size:32px">PROTECT WHAT<br><em>MATTERS</em> MOST</h2>
  <p class="body-copy abs" style="left:205px;top:1623px;width:300px">Whether it's for footy, basketball, martial arts, or any other contact sport, our custom sports mouthguards help prevent serious dental injuries—keeping you safe, confident, and game-ready.</p>
  <div class="btn" style="left:205px;top:1745px">BOOK NOW<span class="dot"><i></i></span></div>
  <div class="media" style="left:618px;top:1505px;width:470px;height:307px;border-radius:6px;background:linear-gradient(135deg,#3a86c9,#1b3a5c 60%,#6fb0de)" role="img" aria-label="Dark blue glitter mouthguard in a clear case"></div>
  <div class="media" style="left:1125px;top:1805px;width:75px;height:130px;border-radius:65px 0 0 65px;background:linear-gradient(135deg,#f4f4f4,#d83a3a)" role="img" aria-label="Red and white patterned mouthguard"></div>

  <!-- game day -->
  <div class="outline-word" style="left:0;top:1908px;color:#e8f7f5">TANDEM MOUTHGUARDS</div>
  <div class="gameday"></div>
  <div class="circle media" style="left:192px;top:1898px;width:196px;height:196px;background:linear-gradient(135deg,#c8201d,#f2d6d0)" role="img" aria-label="Red and pink mouthguards in a case"></div>
  <div class="circle media" style="left:110px;top:1952px;width:128px;height:128px;background:linear-gradient(135deg,#6a48d6,#d63fc8);border-color:var(--teal)" role="img" aria-label="Purple glitter mouthguard"></div>
  <h2 class="gameday h2x" style="all:unset"></h2>
  <div class="abs" style="left:0;top:2025px;width:1200px;text-align:center;color:var(--white);font-size:40px;font-weight:600;line-height:1.15">Now you're<br>ready for game day!</div>
  <div class="gameday-note">Our turnaround time is generally 1–2 weeks, however we may be able to<br>accommodate quicker turnaround times. Contact us for more details.</div>
  <div class="btn" style="left:524px;top:2175px;background:transparent;border:1.5px solid var(--white)">BOOK NOW<span class="dot" style="top:2px;right:2px"><i></i></span></div>

  <svg class="abs" style="left:0;top:2250px" width="1200" height="374" viewBox="0 0 1200 374">
    <path d="M0 155 Q600 -90 1200 155 L1200 374 L0 374Z" fill="var(--navy-deep)"/>
    <path d="M0 150 Q600 -50 1200 150" fill="none" stroke="var(--white)" stroke-width="3"/>
  </svg>
  <div class="abs" style="left:0;top:2318px;width:1200px;display:flex;justify-content:center;align-items:center;gap:8px;color:var(--white);font-size:30px;font-weight:500">
    <svg width="22" height="22" viewBox="0 0 22 22"><circle cx="11" cy="11" r="11" fill="var(--yellow)"/></svg>VELORA
  </div>
  <div class="circle media" style="left:812px;top:2192px;width:188px;height:188px;background:linear-gradient(135deg,#f2eeee,#a4121b)" role="img" aria-label="Maroon club mouthguard in a white case"></div>
  <div class="circle media" style="left:958px;top:2242px;width:116px;height:116px;background:linear-gradient(135deg,#7b3fc8,#59c6c9);border-color:var(--green)" role="img" aria-label="Purple and teal mouthguard in a case"></div>

  <!-- footer -->
  <div class="abs footer-col" style="left:112px;top:2410px;width:160px">
    <div style="color:var(--white);font-weight:800;font-size:11px">HARBOURLINE DENTURE CARE</div>
    <div style="color:var(--white);font-weight:800;font-size:20px;line-height:1.05;margin-top:22px">TANDEM MOUTHGUARDS</div>
    <span style="margin-top:26px;font-size:9px;line-height:1.5">*Gap free mouthguards available to private health members with dental coverage.</span>
  </div>
  <div class="abs footer-col" style="left:401px;top:2410px">
    <h4>MAIN LINKS</h4>
    <a>Home</a><a>About US</a><a>Our Mouthguards</a><a>Photo Gallery</a><a>FAQ</a><a>Contact Us</a>
  </div>
  <div class="abs footer-col" style="left:626px;top:2410px">
    <h4>CONTACT US</h4>
    <div class="contact-row"><b><svg width="10" height="12" viewBox="0 0 10 12"><path d="M5 0a4 4 0 0 1 4 4c0 3-4 8-4 8S1 7 1 4a4 4 0 0 1 4-4z" fill="var(--white)"/><circle cx="5" cy="4" r="1.4" fill="var(--navy)"/></svg></b>Unit 7/14 Kestrel Way, Baywood WA 6120</div>
    <div class="contact-row"><b><svg width="10" height="10" viewBox="0 0 10 10"><path d="M2 0l2 2-1 1.5a6 6 0 0 0 3.5 3.5L8 6l2 2-1.5 2C4 10 0 6 0 1.5z" fill="var(--white)"/></svg></b>08 5550 2718</div>
    <div class="contact-row" style="color:var(--green)"><b><svg width="11" height="8" viewBox="0 0 11 8"><rect width="11" height="8" rx="1" fill="var(--white)"/><path d="M0 0l5.5 4L11 0" stroke="var(--navy)" fill="none"/></svg></b>hello@tandemmouthguards.com.au</div>
  </div>
  <div class="abs footer-col" style="left:967px;top:2410px">
    <h4>FOLLOW US ON</h4>
    <div class="contact-row"><b></b>Friendsy</div>
    <div class="contact-row"><b></b>Snapwall</div>
  </div>
  <div class="abs" style="left:112px;top:2586px;width:976px;height:1px;background:rgba(255,255,255,.25)"></div>
  <div class="abs" style="left:0;top:2602px;width:1200px;text-align:center;color:var(--white);font-size:9px">©2025 Tandem Mouthguards All Rights Reserved.</div>

</div>
</body>
</html>
```